Business Card Design

I already have a company logo for my company. I have a logo for the manufacturer we represent. I want a professional business card design.

```html
<!DOCTYPE html>
<html lang="en">
<head>
<meta charset="utf-8">
<title>Northfield Supply — Business Card</title>
<link rel="stylesheet" href="https://fonts.googleapis.com/css2?family=Open+Sans:wght@400;600;700;800&display=swap">
<style>
  :root {
    --stage: #141417;
    --card: #1f1e23;
    --card-pattern-a: #26252b;
    --card-pattern-b: #1c1b20;
    --edge-red: #e3212b;
    --accent-red: #e3212b;
    --gold: #b8923a;
    --ink: #ffffff;
  }
  * { box-sizing: border-box; margin: 0; padding: 0; }
  html, body {
    width: 1200px; height: 780px; overflow: hidden;
    background: var(--stage);
    font-family: "Open Sans", Arial, sans-serif;
  }
  .canvas {
    width: 1200px; height: 780px;
    display: flex; align-items: center; justify-content: center; gap: 40px;
  }
  .card {
    position: relative;
    width: 540px; height: 309px;
    background: var(--card);
    border: 3px solid var(--edge-red);
    border-radius: 22px;
    overflow: hidden;
  }
  /* Front side */
  .card-front__pattern {
    position: absolute; inset: 0;
    background: linear-gradient(135deg, var(--card-pattern-a), var(--card-pattern-b));
  }
  .brand {
    position: absolute; top: 26px; right: 28px;
    display: flex; align-items: center; gap: 7px;
    font-weight: 700; font-size: 13px; color: var(--ink);
    letter-spacing: 0.02em;
  }
  .brand__mark {
    width: 11px; height: 11px; background: var(--accent-red);
  }
  /* Back side */
  .identity {
    position: absolute; left: 38px; top: 110px;
  }
  .identity__name {
    font-weight: 800; font-size: 30px; line-height: 1.05; color: var(--ink);
  }
  .identity__first { color: var(--accent-red); }
  .identity__role {
    margin-top: 4px; margin-left: 80px;
    font-weight: 600; font-size: 15px; color: var(--ink);
  }
  .divider {
    position: absolute; left: 312px; top: 78px;
    width: 1px; height: 112px;
    background: linear-gradient(180deg, transparent, var(--gold) 25%, var(--gold) 75%, transparent);
  }
  .contacts {
    position: absolute; left: 332px; top: 90px;
    list-style: none;
    display: flex; flex-direction: column; gap: 12px;
  }
  .contacts__item {
    display: flex; align-items: center; gap: 8px;
    font-size: 13px; color: var(--ink);
  }
  .contacts__icon { width: 13px; height: 13px; flex: none; }
  .address {
    position: absolute; left: 0; right: 0; bottom: 34px;
    text-align: center;
    font-size: 15px; color: var(--ink);
  }
</style>
</head>
<body>
<main class="canvas">

  <section class="card card-front" aria-label="Card front">
    <div class="card-front__pattern" role="img" aria-label="Repeating tone-on-tone pattern of the company symbol"></div>
    <div class="brand">
      <span class="brand__mark"></span>
      <span class="brand__name">Northfield Supply</span>
    </div>
  </section>

  <section class="card card-back" aria-label="Card back">
    <div class="identity">
      <p class="identity__name"><span class="identity__first">Marta</span> Kovalenko</p>
      <p class="identity__role">Managing Director</p>
    </div>

    <div class="divider"></div>

    <ul class="contacts">
      <li class="contacts__item">
        <svg class="contacts__icon" viewBox="0 0 24 24" aria-hidden="true">
          <path fill="var(--accent-red)" d="M6.6 10.8a15.1 15.1 0 0 0 6.6 6.6l2.2-2.2a1 1 0 0 1 1-.25 11.4 11.4 0 0 0 3.6.57 1 1 0 0 1 1 1V20a1 1 0 0 1-1 1A17 17 0 0 1 3 4a1 1 0 0 1 1-1h3.5a1 1 0 0 1 1 1c0 1.25.2 2.45.57 3.57a1 1 0 0 1-.25 1z"/>
        </svg>
        (555) 214-0387
      </li>
      <li class="contacts__item">
        <svg class="contacts__icon" viewBox="0 0 24 24" aria-hidden="true">
          <rect x="2" y="5" width="20" height="14" rx="2" fill="var(--accent-red)"/>
          <path d="M3 6.5l9 6.5 9-6.5" fill="none" stroke="var(--card)" stroke-width="1.8"/>
        </svg>
        hello@northfieldco.com
      </li>
      <li class="contacts__item">
        <svg class="contacts__icon" viewBox="0 0 24 24" aria-hidden="true">
          <circle cx="12" cy="12" r="10" fill="var(--accent-red)"/>
          <path d="M2 12h20M12 2c3 3 3 17 0 20M12 2c-3 3-3 17 0 20" fill="none" stroke="var(--card)" stroke-width="1.4"/>
        </svg>
        www.northfieldco.com
      </li>
    </ul>

    <p class="address">418 Cedar Ridge Ave. Suite 120 Lakeview, TX 75001</p>
  </section>

</main>
</body>
</html>
```